Stationery Design Project

Please create a custom Stationery Design for Pinecrest Dwellings. The logo is attached to this brief.

Please Include:
- Letterhead
- With Compliments slip
- Envelope

Please also see open Business Card project: http://briefs.sketchvault.example/task.aspx?id=517290

Industry/Entity Type

Business

```html
<!DOCTYPE html>
<html lang="en">
<head>
<meta charset="utf-8">
<title>Pinecrest Dwellings Stationery</title>
<link href="https://fonts.googleapis.com/css2?family=Source+Sans+3:wght@400;600&display=swap" rel="stylesheet">
<style>
:root{
  --backdrop:#5e5e5e;
  --paper:#ffffff;
  --brand-blue:#0a6fba;
  --brand-green:#8cc63f;
  --ink-grey:#555555;
  --faint-grey:#e4e4e4;
  --rule-grey:#b8b8b8;
}
*{margin:0;padding:0;box-sizing:border-box}
html,body{width:1200px;height:640px;overflow:hidden;background:var(--backdrop)}
body{position:relative;font-family:"Source Sans 3",Arial,sans-serif}
.sheet{position:absolute;background:var(--paper);overflow:hidden;box-shadow:2px 3px 6px rgba(0,0,0,.35)}
.sheet svg.wave{position:absolute;left:0;top:0;width:100%;height:100%}
.brand-name{font-family:"Source Sans 3",Arial,sans-serif;font-weight:600;color:var(--brand-blue);display:flex;align-items:center;gap:5px;white-space:nowrap}
.brand-mark{border-radius:50%;background:var(--brand-blue);flex:none}
.contact{color:var(--ink-grey);font-size:5.5px;line-height:8px;border-left:1px solid var(--rule-grey);padding-left:4px;white-space:nowrap}
.contact .icon{display:inline-block;width:5px;height:5px;background:var(--brand-blue);border-radius:1px;margin-right:3px;vertical-align:-0.5px}
.faint-mark{position:absolute;border-radius:50%;background:var(--faint-grey)}

/* footer row: brand name followed by contact blocks, laid out so they never collide */
.footer-row{position:absolute;display:flex;align-items:center;gap:12px}

/* letterhead */
.letterhead{left:80px;top:58px;width:372px;height:526px}
.letterhead .brand-name{position:absolute;left:28px;top:44px;font-size:13px}
.letterhead .contact{position:absolute;left:256px;top:50px}
.letterhead .faint-mark{left:126px;top:200px;width:120px;height:120px}

/* envelope front */
.envelope-front{left:531px;top:24px;width:446px;height:177px}
.envelope-front .footer-row{left:30px;top:138px}
.envelope-front .brand-name{font-size:12px}
.envelope-front .faint-mark{left:340px;top:66px;width:96px;height:96px}

/* envelope back */
.envelope-back{left:724px;top:230px;width:446px;height:178px}
.envelope-back .brand-name{position:absolute;left:0;right:0;top:22px;justify-content:center;font-size:11px}

/* compliments slip */
.compliments{left:558px;top:438px;width:364px;height:160px}
.compliments .greeting{position:absolute;right:28px;top:36px;color:var(--brand-blue);font-size:13.5px;font-weight:400}
.compliments .footer-row{left:22px;top:120px;gap:10px}
.compliments .brand-name{font-size:11px}
.compliments .contact{font-size:4.8px;line-height:7px}
</style>
</head>
<body>

<section class="sheet letterhead">
  <svg class="wave" viewBox="0 0 372 526" preserveAspectRatio="none" aria-hidden="true">
    <path d="M0 455 C90 440 200 455 290 495 C330 512 355 490 372 470 L372 526 L0 526 Z" fill="var(--brand-blue)"/>
    <path d="M0 444 C110 430 230 450 300 490 C230 456 110 440 0 452 Z" fill="var(--brand-green)"/>
  </svg>
  <div class="brand-name"><span class="brand-mark" style="width:9px;height:9px"></span>Pinecrest Dwellings</div>
  <div class="contact">
    <div><span class="icon"></span>020 7391 4820</div>
    <div><span class="icon"></span>www.pinecrestdwellings.example</div>
    <div>12 Alder Court, Address Line</div>
    <div>Millbrook Business Park, City Name</div>
  </div>
  <div class="faint-mark" role="img" aria-label="Faint brand emblem"></div>
</section>

<section class="sheet envelope-front">
  <svg class="wave" viewBox="0 0 446 177" preserveAspectRatio="none" aria-hidden="true">
    <path d="M0 0 L446 0 L446 50 C400 20 330 15 240 30 C150 45 70 52 0 50 Z" fill="var(--brand-blue)"/>
    <path d="M0 58 C120 56 220 30 370 22 C230 34 120 66 0 66 Z" fill="var(--brand-green)"/>
    <rect x="0" y="164" width="446" height="3" fill="var(--brand-green)"/>
    <rect x="0" y="170" width="446" height="7" fill="var(--brand-blue)"/>
  </svg>
  <div class="faint-mark" role="img" aria-label="Faint brand emblem"></div>
  <div class="footer-row">
    <div class="brand-name"><span class="brand-mark" style="width:8px;height:8px"></span>Pinecrest Dwellings</div>
    <div class="contact">
      <div>12 Alder Court, Address Line</div>
      <div>Millbrook Business Park, City Name</div>
    </div>
  </div>
</section>

<section class="sheet envelope-back">
  <svg class="wave" viewBox="0 0 446 178" preserveAspectRatio="none" aria-hidden="true">
    <path d="M0 0 L0 22 C0 40 10 48 26 50 L420 50 C436 48 446 40 446 22 L446 0" fill="none" stroke="var(--rule-grey)" stroke-width="1"/>
  </svg>
  <div class="brand-name"><span class="brand-mark" style="width:7px;height:7px"></span>Pinecrest Dwellings</div>
</section>

<section class="sheet compliments">
  <svg class="wave" viewBox="0 0 364 160" preserveAspectRatio="none" aria-hidden="true">
    <path d="M0 0 L364 0 L364 48 C320 22 250 16 180 26 C110 36 50 42 0 40 Z" fill="var(--brand-blue)"/>
    <path d="M0 46 C100 44 180 24 300 18 C190 30 100 54 0 54 Z" fill="var(--brand-green)"/>
    <rect x="0" y="148" width="364" height="3" fill="var(--brand-green)"/>
    <rect x="0" y="153" width="364" height="7" fill="var(--brand-blue)"/>
  </svg>
  <div class="greeting">With Compliments</div>
  <div class="footer-row">
    <div class="brand-name"><span class="brand-mark" style="width:7px;height:7px"></span>Pinecrest Dwellings</div>
    <div class="contact">
      <div>12 Alder Court, Address Line</div>
      <div>Millbrook Business Park, City Name</div>
    </div>
    <div class="contact">
      <div><span class="icon"></span>020 7391 4820</div>
      <div><span class="icon"></span>www.pinecrestdwellings.example</div>
    </div>
  </div>
</section>

</body>
</html>
```